A 'new law' boutique Australian law firm that provides specialist employment law and people managem

We value helping clients create results with respect workplaces. What differentiates us is we provide actionable training in understanding and dealing with people and ensure legal compliance fits with this approach. We would like a fresh approach to our training overview documents that we currently use in our current law firm (6 attached). Please use pictures, symbols etc consistent with our non-traditional law approach that captures the approach of each training session.. Attached is the logo and draft letterhead for Birchwell Legal which will launch soon.

Target Market(s)

HR Managers and in-house lawyers (non employment specialists) in mid-large Australian companies that are progressive with a relationship based approach to managing employee behaviours and disputes.

Industry/Entity Type

Human Resource

Font styles to use
Sans Serif

Colors
3176b5
33a6d7

Requirements
Must have
• 1 or 2 page PDF for each of the 6 documents that the wording supplied goes into your design which will be pretty similar as we want consistency with our documents

```html
<!DOCTYPE html>
<html lang="en">
<head>
<meta charset="utf-8">
<title>Contact Officer Training – Birchwell Legal</title>
<link href="https://fonts.googleapis.com/css2?family=Exo+2:wght@700;800&family=Open+Sans:wght@400;600;700&display=swap" rel="stylesheet">
<style>
  :root {
    --brand-blue: #1668b3;
    --band-blue: #1d5fae;
    --row-blue: #1876c0;
    --label-blue: #3d86c6;
    --sky: #33a6d7;
    --charcoal: #3a3a3c;
    --ink: #222;
    --paper: #ffffff;
  }
  * { box-sizing: border-box; margin: 0; padding: 0; }
  html, body { width: 896px; height: 1200px; overflow: hidden; background: var(--paper); }
  body { position: relative; font-family: "Open Sans", Arial, sans-serif; color: var(--ink); }

  .hero { position: absolute; inset: 0 0 auto 0; height: 272px; overflow: hidden; }
  .hero-photo {
    position: absolute; right: 0; top: 0; width: 620px; height: 272px;
    background: linear-gradient(90deg, rgba(255,255,255,1) 0%, rgba(225,228,233,0.7) 30%, #9aa2ac 60%, #6f5140 78%, #c9a97c 92%, #8c8f95 100%);
  }
  .hero-title { position: absolute; left: 55px; top: 70px; font-family: "Exo 2", Arial, sans-serif; color: var(--brand-blue); line-height: 0.9; }
  .hero-title .kicker { display: block; font-size: 47px; font-weight: 800; letter-spacing: -0.5px; }
  .hero-title .main { display: block; font-size: 93px; font-weight: 800; letter-spacing: -2px; margin-top: 2px; }

  .section-band { position: absolute; left: 0; top: 272px; width: 896px; height: 52px; }
  .section-band svg { position: absolute; inset: 0; }
  .section-band h2 { position: absolute; left: 40px; top: 10px; color: #fff; }

  h2 { font-family: "Exo 2", Arial, sans-serif; font-weight: 800; font-size: 27px; letter-spacing: -0.3px; }

  .need { position: absolute; top: 344px; left: 48px; right: 40px; display: grid; grid-template-columns: 1fr 1fr; column-gap: 30px; font-size: 12.4px; line-height: 1.4; }
  .need p + p { margin-top: 14px; }

  .overview-title { position: absolute; left: 40px; top: 522px; color: var(--band-blue); }

  .overview { position: absolute; left: 36px; top: 558px; width: 825px; display: grid; grid-template-columns: 222px 1fr; font-size: 10.6px; line-height: 1.33; color: #fff; }
  .overview .topic, .overview .detail { border-bottom: 2px solid #fff; padding: 10px 26px; }
  .overview .topic { background: var(--label-blue); border-right: 2px solid #fff; }
  .overview .detail { background: var(--row-blue); display: flex; align-items: center; }
  .overview .tall { height: 60px; }
  .overview .short { height: 32px; }

  .outcomes-title { position: absolute; left: 40px; top: 996px; color: var(--band-blue); }
  .outcomes-lead { position: absolute; left: 40px; top: 1034px; font-size: 12.4px; font-weight: 700; }
  .outcomes { position: absolute; left: 40px; top: 1056px; list-style: none; font-size: 12.6px; line-height: 1.27; }

  .firm { position: absolute; left: 640px; top: 1080px; width: 230px; display: flex; align-items: center; gap: 10px; }
  .firm .dot { width: 26px; height: 26px; border-radius: 50%; background: var(--brand-blue); flex: none; }
  .firm .name { font-family: "Open Sans", Arial, sans-serif; font-weight: 700; font-size: 24px; color: var(--brand-blue); white-space: nowrap; }

  .footer-band { position: absolute; left: 0; bottom: 0; width: 896px; height: 16px; }
</style>
</head>
<body>
  <header class="hero">
    <div class="hero-photo" role="img" aria-label="Wooden gavel resting on a law book in front of a row of bound legal volumes"></div>
    <h1 class="hero-title"><span class="kicker">CONTACT OFFICER</span><span class="main">TRAINING</span></h1>
  </header>

  <div class="section-band">
    <svg width="896" height="52" viewBox="0 0 896 52" aria-hidden="true">
      <rect width="896" height="52" fill="var(--band-blue)"/>
      <path d="M250 0 H896 V22 C700 10 560 6 250 0 Z" fill="var(--charcoal)"/>
      <path d="M330 52 C520 30 700 24 896 30 V52 Z" fill="var(--sky)" opacity="0.55"/>
    </svg>
    <h2>TRAINING NEED</h2>
  </div>

  <section class="need">
    <div>
      <p>Unlawful or inappropriate behavior in the workplace that is left unaddressed can impact on productivity and employee retention.&nbsp; Claims can be costly in terms of time and money as well as the impact on mental health from being involved in uncomfortable adversarial processes.</p>
      <p>Clear policies and procedures explaining the organisation’s workplace behavior expectations and how grievances will be managed are a minimum compliance requirement.</p>
    </div>
    <div>
      <p>The challenge is ensuring that employees understand the directions contained in those policies, what is unlawful and inappropriate behaviour and the options available to address those behaviours if they experience them or engage in them.</p>
      <p>Well trained Contact Officers provide another resource to assist the organisation to provide a safe and respectful workplace.</p>
    </div>
  </section>

  <h2 class="overview-title">OVERVIEW</h2>
  <section class="overview">
    <div class="topic tall">Discrimination</div>
    <div class="detail tall">What is direct and indirect discrimination? What are the prescribed attributes?<br>What are the exceptions to the general rules.<br>Practical examples of behaviour that may be discriminatory.</div>

    <div class="topic tall">Harassment</div>
    <div class="detail tall">What is harassment?&nbsp; Are protected attributes relevant to harassment? What is the difference between harassment and sexual harassment?&nbsp; How does the reasonable person test work in relation to harassment? Practical examples of behaviour that may be harassment or sexual harassment.</div>

    <div class="topic tall">Bullying</div>
    <div class="detail tall">What is bullying. Explore how bullying differs to discrimination or inappropriate behaviour. Performance Management - when it will and will not be bullying. Is all workplace conflict bullying?<br>Practical examples of behaviour that may be bullying.</div>

    <div class="topic short">Victimisation and Vilification</div>
    <div class="detail short">What is victimisation? What is Vilification?</div>

    <div class="topic tall">Adverse Action</div>
    <div class="detail tall">What is adverse action and how does it differ to other unlawful behaviour? What is a workplace right?<br>When is it lawful to terminate employment because of an employee’s absence?<br>How are the protected attributes relevant to adverse action?</div>

    <div class="topic tall">The Contact Officer’s role</div>
    <div class="detail tall">How to perform your role when approached by an employee – the 6 step approach. What not to do.<br>What are the obligations with regard to Confidentiality?</div>

    <div class="topic tall">Grievance Options</div>
    <div class="detail tall">Explore the options of complaint management - self management, internal informal management, formal internal management.&nbsp; How do they compare and what are the advantages and disadvantages of each approach. Is doing nothing an option? External options – advantages and disadvantages. Who decides which option?</div>

    <div class="topic short">Test Learning</div>
    <div class="detail short">Role play, group discussion</div>
  </section>

  <h2 class="outcomes-title">LEARNING OUTCOMES</h2>
  <p class="outcomes-lead">Training will enable participants to perform their role of Contact Officer and to understand:</p>
  <ol class="outcomes">
    <li>1 The role and responsibilities of a Contact Officer</li>
    <li>2 What amounts to unlawful workplace behaviour</li>
    <li>3 What is considered inappropriate behaviour in our workplace</li>
    <li>4 How to apply understanding unlawful/inappropriate behaviour to common scenarios</li>
    <li>5 How to address and resolve grievances early</li>
    <li>6 Options to resolve grievances internally and the Contact Officer role</li>
    <li>7 External options and their pros and cons for resolving grievances</li>
  </ol>

  <div class="firm">
    <span class="dot"></span>
    <span class="name">Birchwell Legal</span>
  </div>

  <svg class="footer-band" width="896" height="16" viewBox="0 0 896 16" aria-hidden="true">
    <rect width="896" height="16" fill="var(--band-blue)"/>
    <path d="M0 0 H300 L260 16 H0 Z" fill="var(--sky)" opacity="0.6"/>
  </svg>
</body>
</html>
```